Corvane Systems Web Site

Need a complete redesign of the website to make it cleaner and up to date.
Current website: http://www.corvanesystems.example/
I am looking for a single page design focused on giving all the information about the POC (Pump Off Controller). And highlighting its benefits: Increased oil production, quick ROI, ease of use and low maintenance cost.
Here's a presentation of the product:
http://slidewharf.example/qk4mtz8vn2ra/?utm_campaign=share&utm_medium=copy&rc=ex0share
Please consider participating on the flyer design:
http://jobs.artmarket.example/job.aspx?id=391726
Here are some design examples of web sites I like:
http://www.bright-harbor.example/
I just added the source files for our business cards. I would like to see designs that incorporate the "tag cloud" on the back of the card..
Target Market(s)
Oil field decision makers. Engineers and technicians from 20 to 60.
Investors and venture capitalists.
Industry/Entity Type
Cleaner
Requirements
Must have
- Single page design
Nice to have
- Responsive web design

```html
<!DOCTYPE html>
<html lang="en">
<head>
<meta charset="utf-8">
<title>Corvane Systems</title>
<link href="https://fonts.googleapis.com/css2?family=Lato:ital,wght@0,400;0,700;0,900;1,400&display=swap" rel="stylesheet">
<style>
:root{
  --blue:#2e3192;
  --blue-dark:#262a80;
  --red:#e52b2e;
  --ink:#333333;
  --muted:#666666;
  --line:#dddddd;
  --footer:#262626;
  --footer-deep:#1a1a1a;
  --panel:#3a3a3a;
  --white:#ffffff;
}
*{margin:0;padding:0;box-sizing:border-box}
html,body{width:770px;height:1200px;overflow:hidden;background:var(--white)}
body{font-family:'Lato',sans-serif;color:var(--ink);position:relative}
.abs{position:absolute}

/* header */
.topbar{left:0;top:0;width:770px;height:52px;background:var(--white)}
.brand{left:82px;top:8px;height:44px;display:flex;align-items:center;gap:8px;z-index:3}
.brand-mark{width:26px;height:26px;border-radius:50%;background:var(--red)}
.brand-name{font-weight:900;font-size:22px;color:var(--blue);letter-spacing:.5px}
.contact-top{top:18px;font-size:11px;color:var(--ink);display:flex;align-items:center;gap:6px}
.contact-top svg{width:14px;height:14px}
.login{left:622px;top:15px;width:64px;height:21px;background:var(--red);color:var(--white);font-size:10px;font-weight:700;display:flex;align-items:center;justify-content:center;gap:5px}
.nav{left:0;top:52px;width:770px;height:28px;background:var(--blue)}
.nav a{position:absolute;top:0;height:28px;line-height:28px;color:var(--white);font-size:10px;font-weight:700;text-decoration:none;text-align:center}
.nav .active{background:var(--red)}

/* hero */
.hero{left:0;top:80px;width:770px;height:288px;background:linear-gradient(180deg,#4f7fb8 0%,#9fbddc 45%,#c9d3da 62%,#8c8272 78%,#6b5d48 100%)}
.callout{left:402px;top:192px;width:303px;height:84px}
.callout svg{position:absolute;left:0;top:0}
.callout p{position:relative;padding:9px 20px 0 28px;color:var(--white);font-size:14.5px;font-weight:700;line-height:21px}

/* about / video */
.section-title{font-size:17px;font-weight:900;color:var(--blue);text-transform:uppercase;padding-bottom:9px;border-bottom:1px solid var(--line)}
.about{left:84px;top:394px;width:340px;height:180px}
.about .lead{margin-top:13px;font-size:9px;font-weight:700;line-height:13.5px;color:var(--ink)}
.about .body{margin-top:8px;font-size:8.4px;line-height:12.5px;color:var(--muted)}
.btn{display:inline-block;background:var(--red);color:var(--white);font-size:9.5px;text-transform:uppercase;padding:5px 9px}
.about .btn{position:absolute;left:0;top:154px}
.video{left:452px;top:394px;width:234px}
.video-frame{margin-top:13px;width:234px;height:138px;position:relative;background:linear-gradient(180deg,#8fb1d4 0%,#c2d3e2 50%,#9a8668 75%,#5e4e38 100%)}
.play{position:absolute;left:100px;top:50px;width:34px;height:34px;border-radius:50%;background:var(--white)}
.play:after{content:"";position:absolute;left:13px;top:10px;border-left:11px solid #222;border-top:7px solid transparent;border-bottom:7px solid transparent}
.controls{position:absolute;left:0;bottom:0;width:234px;height:14px;background:#1c1c1c;color:var(--white);font-size:7px;display:flex;align-items:center;gap:5px;padding:0 5px}
.track{flex:1;height:3px;background:#555;position:relative}
.track i{position:absolute;left:0;top:0;width:22%;height:3px;background:#3d7fd6}

/* features */
.features{left:0;top:602px;width:770px;height:204px;background:radial-gradient(ellipse at center,#3b3fa6 0%,var(--blue) 55%,var(--blue-dark) 100%)}
.card{position:absolute;top:22px;width:140px;height:160px;background:var(--white);padding:5px;text-align:center}
.card .photo{height:80px;background:linear-gradient(180deg,#7ea4cc 0%,#b7c9db 55%,#6f6352 100%)}
.card h3{margin-top:14px;font-size:8.5px;font-weight:700;line-height:12px;color:var(--ink);height:24px}
.card .btn{margin-top:11px;font-size:8.5px;padding:4px 8px}

/* feedback */
.feedback-title{left:0;top:832px;width:770px;text-align:center;font-size:17px;font-weight:900;color:var(--blue);text-transform:uppercase}
.quote{left:93px;top:870px;width:530px;height:68px;background:#f1f1f1;padding:10px 30px 0 40px;font-size:8px;font-style:italic;line-height:14px;color:var(--muted)}
.quote-mark{left:100px;top:874px;font-size:36px;font-weight:900;color:#c8c8c8;line-height:1}
.avatar{left:607px;top:868px;width:72px;height:72px;border-radius:50%;background:linear-gradient(180deg,#d9dde2,#9aa3ad);border:3px solid var(--white);box-shadow:0 0 0 1px var(--line)}
.cite{left:410px;top:946px;width:197px;text-align:right;font-size:8px;font-style:italic;color:var(--ink)}
.rule{left:84px;top:984px;width:602px;height:1px;background:var(--line)}

/* partners */
.partners{left:84px;top:1006px;width:602px;display:flex;justify-content:space-between;font-size:12px;font-weight:700;color:#555}

/* footer */
.footer{left:0;top:1040px;width:770px;height:135px;background:var(--footer)}
footer h4{font-size:11px;font-weight:700;color:var(--white);text-transform:uppercase}
.links{left:86px;top:1060px}
.links ul{list-style:none;margin-top:10px}
.links li{font-size:8.5px;color:#cfcfcf;line-height:15px;padding-left:10px;position:relative}
.links li:before{content:"";position:absolute;left:0;top:5px;border-left:4px solid #cfcfcf;border-top:3px solid transparent;border-bottom:3px solid transparent}
.contact{left:250px;top:1060px;width:150px}
.contact .row{display:flex;gap:8px;margin-top:10px;font-size:8.5px;color:#cfcfcf;line-height:12px}
.contact .row svg{flex:none;width:10px;height:10px;margin-top:1px}
.contact .phone{font-size:11px;font-weight:700;color:var(--white)}
.newsletter{left:412px;top:1058px;width:274px;height:108px;background:var(--panel);padding:12px 12px}
.newsletter .corner{position:absolute;right:0;top:0;border-top:14px solid var(--red);border-left:14px solid transparent}
.newsletter h4{font-size:13px}
.newsletter p{width:116px;margin-top:6px;font-size:8px;line-height:11px;color:#d6d6d6}
.field{position:absolute;left:132px;width:120px;height:16px;background:#222;color:#cfcfcf;font-size:8px;font-style:italic;padding-left:18px;line-height:16px}
.field svg{position:absolute;left:5px;top:4px;width:8px;height:8px}
.subscribe{position:absolute;left:132px;top:84px;background:var(--red);color:var(--white);font-size:8px;padding:3px 7px;text-transform:uppercase}
.copyright{left:0;top:1175px;width:770px;height:25px;background:var(--footer-deep);color:#d6d6d6;font-size:9px;text-align:center;line-height:25px}
</style>
</head>
<body>

<header>
  <div class="abs topbar"></div>
  <div class="abs brand"><span class="brand-mark"></span><span class="brand-name">CORVANE</span></div>
  <div class="abs contact-top" style="left:362px">
    <svg viewBox="0 0 16 16"><circle cx="8" cy="8" r="8" fill="#e5e5e5"/><path d="M5.5 4.5l1.5 0 .8 2-1 .8a5 5 0 0 0 2 2l.8-1 2 .8v1.5a1 1 0 0 1-1 1 7 7 0 0 1-6-6 1 1 0 0 1 1-1z" fill="#555"/></svg>
    (555) 013 4470
  </div>
  <div class="abs contact-top" style="left:468px">
    <svg viewBox="0 0 16 16"><circle cx="8" cy="8" r="8" fill="#e5e5e5"/><rect x="4" y="5.5" width="8" height="5.5" fill="#555"/><path d="M4 5.5l4 3 4-3" stroke="#e5e5e5" fill="none"/></svg>
    info@corvanesystems.com
  </div>
  <div class="abs login">
    <svg width="9" height="9" viewBox="0 0 10 10"><circle cx="5" cy="3" r="2.3" fill="#fff"/><path d="M1 10a4 4 0 0 1 8 0z" fill="#fff"/></svg>
    LOGIN
  </div>
  <nav class="abs nav">
    <a class="active" href="#" style="left:297px;width:59px">HOME</a>
    <a href="#" style="left:370px;width:56px">COMPANY</a>
    <a href="#" style="left:452px;width:58px">PRODUCTS</a>
    <a href="#" style="left:536px;width:60px">TELEMETRY</a>
    <a href="#" style="left:620px;width:72px">CONTACT US</a>
  </nav>
</header>

<section class="abs hero" role="img" aria-label="Pump jack working an oil well under a blue sky with distant mountains"></section>
<div class="abs callout">
  <svg width="303" height="84" viewBox="0 0 303 84"><polygon points="8,0 303,0 295,84 0,84" fill="#e52b2e"/></svg>
  <p>Are Your Well Running Under A Timer Switch? Have You Thought Of Increasing The Barrel Count At Each Well? Corvane CAN Do It!</p>
</div>

<section class="abs about">
  <h2 class="section-title">About Corvane</h2>
  <p class="lead">Lorem ipsum dolor sit amet, consectetur adipisicing elit, sed do eiusmod tem incididunt ut labore et dolore magna aliqua. Ut enim ad minim veniam.</p>
  <p class="body">Duis aute irure dolor in reprehenderitnin voluptate velit esse cillum dolore eu fugiat nulla pariatur. Excepteur sint occaecat cupidatat non proident, sunt in culpa qui officia deserunt mollit anim id est laborum Neque porro quisquam est, qui dolorem ipsum quia consectetur adipisci velit, sed quia non numquam eius modi tempora incidunt ut labore et dol magnam aliquam quaerat voluptatem. Ut enim ad minima veniam, quis nostrum exer ullam corporis suscipit laboriosam nisi ut aliquid ex ea commodi consequatur.</p>
  <span class="btn">Read More</span>
</section>

<section class="abs video">
  <h2 class="section-title">Our Video</h2>
  <div class="video-frame" role="img" aria-label="Video still of pump jacks in an oil field">
    <span class="play"></span>
    <div class="controls"><span>&#9654;</span><span>04:08</span><span class="track"><i></i></span><span>10:35</span><span>&#9632;</span></div>
  </div>
</section>

<section class="abs features">
  <article class="card" style="left:84px">
    <div class="photo" role="img" aria-label="Pump jack silhouetted against the sky"></div>
    <h3>High Reliability and<br>Accessibility</h3>
    <span class="btn">Read More</span>
  </article>
  <article class="card" style="left:238px">
    <div class="photo" role="img" aria-label="Engineers reviewing reports at a desk" style="background:linear-gradient(180deg,#e7e9ec,#9aa4b0)"></div>
    <h3>Alarm Generation and<br>Reporting</h3>
    <span class="btn">Read More</span>
  </article>
  <article class="card" style="left:392px">
    <div class="photo" role="img" aria-label="Pump jacks at sunset" style="background:linear-gradient(180deg,#f0c37a,#c9854a 60%,#3b2a1e)"></div>
    <h3>Cost Savings due to improved<br>Pumper Efficiency</h3>
    <span class="btn">Read More</span>
  </article>
  <article class="card" style="left:546px">
    <div class="photo" role="img" aria-label="Technician inspecting pipes at a processing plant" style="background:linear-gradient(180deg,#aac4dc,#d2d7dc 55%,#8c8f93)"></div>
    <h3>Data<br>Security</h3>
    <span class="btn">Read More</span>
  </article>
</section>

<h2 class="abs feedback-title">Customer Feedback</h2>
<div class="abs quote">Lorem sum dolor sit amet, consectetuer adipiscing elit, sed diam nonummy nibh euismod tincidunt ut laoreet re agn aliquam erat volutpat wisi enim ad minim veniam, quis nostrud exerci tation ullamcorper suscipit lobortis nisl ut aliquip modo consequatis autem vel eum iriure dolor in hendrerit in vulputate velit esse molestie consequat, vel illum dolore eu.</div>
<div class="abs quote-mark">&ldquo;</div>
<div class="abs avatar" role="img" aria-label="Customer portrait"></div>
<div class="abs cite">Dalen Ruiz, Northfield , USA</div>
<div class="abs rule"></div>

<div class="abs partners">
  <span>VERANTO</span><span>Kelmwood</span><span>plinth</span><span>Brightfold</span><span>Ostrava</span><span>Halden</span><span>Marrowby</span><span>Quillstone</span>
</div>

<footer>
  <div class="abs footer"></div>
  <div class="abs links">
    <h4>Quick Links</h4>
    <ul><li>Home</li><li>Company</li><li>Products</li><li>Telemetry</li><li>Contact Us</li></ul>
  </div>
  <div class="abs contact">
    <h4>Contact Detail</h4>
    <div class="row"><svg viewBox="0 0 10 10"><path d="M5 0a3.5 3.5 0 0 1 3.5 3.5C8.5 6 5 10 5 10S1.5 6 1.5 3.5A3.5 3.5 0 0 1 5 0z" fill="#cfcfcf"/><circle cx="5" cy="3.5" r="1.3" fill="#262626"/></svg><span>480 Ridgeback Road<br>Suite #212 Marlow, Tx 79000</span></div>
    <div class="row"><svg viewBox="0 0 10 10"><path d="M2 1h2l.7 2-1 .8a4 4 0 0 0 2.5 2.5l.8-1 2 .7v2a1 1 0 0 1-1 1A8 8 0 0 1 1 2a1 1 0 0 1 1-1z" fill="#cfcfcf"/></svg><span class="phone">(555) 013 4470</span></div>
    <div class="row"><svg viewBox="0 0 10 10"><rect x="0" y="2" width="10" height="6.5" fill="#cfcfcf"/><path d="M0 2l5 3.5L10 2" stroke="#262626" fill="none"/></svg><span>info@corvanesystems.com</span></div>
  </div>
  <div class="abs newsletter">
    <span class="corner"></span>
    <h4>Newsletter</h4>
    <p>Get Valuable Tips and News from Corvane. Signup to our Monthly Newsletter today!</p>
    <div class="field" style="top:26px"><svg viewBox="0 0 10 10"><circle cx="5" cy="3" r="2.3" fill="#aaa"/><path d="M1 10a4 4 0 0 1 8 0z" fill="#aaa"/></svg>Name</div>
    <div class="field" style="top:51px"><svg viewBox="0 0 10 10"><rect x="0" y="2" width="10" height="6.5" fill="#aaa"/><path d="M0 2l5 3.5L10 2" stroke="#222" fill="none"/></svg>Email</div>
    <span class="subscribe">Subscribe</span>
  </div>
  <div class="abs copyright">Copyright &copy; 2014 - CORVANE</div>
</footer>

</body>
</html>
```